Professional, Attractive, Simple Website Needed!!

We completed the design for our logo.

We need a website built out around this.

Here are a couple samples of how we want ours formatted.

http://brimvoltco.com

http://www.ravelbeam.com/lp/free-quote?LeadSource=Search%20Engine&ProgramName=searchads&experience=qual&language=en&type=brd&gclid=Xk7PLmqwTRZBNVuEYcaHdFgWsLoPeRtQnMxVbCzJaKiOuYtReWqAsDfGhJkLzXcVbNmQwErTyUiOpAsDfGhJkLzX_wcB

http://quorel.co
Updates

Project Deadline Extended
Reason: Extending this deadline due to our delay in providing designers with content for each page. This is coming in next 24 hours.

Project Deadline Extended
Reason: Due to scheduling conflicts and extended travel delays related to Puerto Rico, the deadline has been extended. Your patience is greatly appreciated.

Project Deadline Extended
Reason: Travel and scheduling conflicts have made it impossible to give this project the thorough review it deserves, therefore I am extending the deadline. Thank you for your patience!

Target Market(s)

Home Owners who earn 60k + household annually

Industry/Entity Type

It Professional

Coding

Coded - Design and coding required

Number of Pages Required

5+ page

Font styles to use
Serif

Colors
34a7d8
9bcb3c

Requirements
Must have
• Simple
• Lead form Entry (Ability for visitor to enter Name, number and address for a quote)
• Sleek Design
• Professional
• Testimonials
• Use color Scheme of Design Logo Attached
Nice to have
• Video when site starts
• Like this
• https://www.vidplexa.com/watch?v=Qm8rTbLw3Np&feature=vidplexa.be
Should not have
• Should not include Commercial solar
• Should not include wind power

```html
<!DOCTYPE html>
<html lang="en">
<head>
<meta charset="utf-8">
<title>Solvane Energy</title>
<link href="https://fonts.googleapis.com/css2?family=Poppins:wght@400;500;600;700&family=Arimo:wght@400;700&family=Lora:ital@1&display=swap" rel="stylesheet">
<style>
:root{
  --green:#8cc63f;
  --blue:#34a7d8;
  --footer:#1192d3;
  --ink:#222;
  --muted:#777;
  --form:#4a4a4a;
  --soft:#f5f6f7;
  --white:#fff;
}
*{margin:0;padding:0;box-sizing:border-box}
html,body{width:1200px;height:2490px;overflow:hidden}
body{position:relative;background:var(--white);font-family:"Arimo",sans-serif;color:var(--ink)}
.abs{position:absolute}
.top-line{left:0;top:0;width:1200px;height:3px;background:var(--blue)}
.site-header{left:0;top:3px;width:1200px;height:89px;background:var(--white)}
.brand-disc{left:83px;top:-16px;width:190px;height:190px;border-radius:50%;background:var(--white);z-index:5;display:flex;align-items:center;justify-content:center}
.brand-name{font-family:"Poppins",sans-serif;font-weight:600;font-size:22px;color:var(--blue);text-align:center;line-height:1.1}
.main-nav{top:37px;font-family:"Poppins",sans-serif;font-size:13px;color:#333;white-space:nowrap}
.main-nav.active{color:var(--green)}
.search-btn{left:1060px;top:20px;width:54px;height:54px;border-radius:50%;border:2px solid var(--green);display:flex;align-items:center;justify-content:center}
.hero{left:0;top:92px;width:1200px;height:600px;background:linear-gradient(180deg,#6fa6d9 0%,#a9c8e6 35%,#b7b0a4 62%,#6f8f4a 85%,#5a7d3a 100%);clip-path:polygon(0 0,100% 0,100% 100%,50% 82%,0 100%)}
.hero-title{left:0;top:180px;width:1200px;text-align:center;font-family:"Poppins",sans-serif;font-weight:700;font-size:40px;color:var(--green)}
.hero-sub{left:0;top:238px;width:1200px;text-align:center;font-family:"Poppins",sans-serif;font-size:20px;color:var(--white)}
.play{left:558px;top:277px}
.lead-form{left:438px;top:452px;width:324px;height:332px;background:var(--form)}
.lead-form h2{position:absolute;top:18px;width:100%;text-align:center;font-family:"Poppins",sans-serif;font-weight:500;font-size:26px;color:var(--white)}
.field{position:absolute;left:25px;width:276px;height:42px;background:var(--white);font-size:12px;color:#555;padding:13px 14px}
.submit{position:absolute;left:25px;top:270px;width:276px;height:42px;background:var(--green);color:var(--white);font-family:"Poppins",sans-serif;font-weight:500;font-size:17px;text-align:center;line-height:42px}
.section-title{left:0;width:1200px;text-align:center;font-family:"Poppins",sans-serif;font-weight:500;font-size:28px;color:var(--green)}
.section-lede{left:200px;width:800px;text-align:center;font-size:12px;line-height:25px;color:var(--muted)}
.step{width:220px;text-align:center}
.step h3{font-family:"Poppins",sans-serif;font-weight:600;font-size:17px;line-height:21px;color:var(--ink)}
.step p{font-size:12px;line-height:22px;color:var(--muted);margin-top:14px}
.testimonials{left:0;top:1288px;width:1200px;height:405px;background:var(--soft)}
.avatar{width:86px;height:86px;border-radius:50%;border:3px solid #ddd;background:linear-gradient(160deg,#c9a58c,#7d6a5e)}
.quote{width:235px;font-size:12px;line-height:22px;color:var(--muted)}
.quote b{font-family:Georgia,serif;font-size:20px;color:#999;margin-right:6px}
.reviewer{font-family:"Poppins",sans-serif;font-weight:600;font-size:12px;color:var(--green)}
.posted{font-size:12px;color:#333}
.stars{font-size:12px;color:var(--green);letter-spacing:1px}
.blog-img{width:329px;height:198px}
.blog-title{font-family:"Poppins",sans-serif;font-weight:500;font-size:19px;color:#333}
.blog-text{width:340px;font-size:12px;line-height:23px;color:var(--muted)}
.blog-meta{font-family:"Lora",serif;font-style:italic;font-size:13px;color:var(--green);display:flex;align-items:center;gap:6px}
.blog-meta svg{flex:none}
.site-footer{left:0;top:2185px;width:1200px;height:305px;background:var(--footer);color:var(--white)}
.foot-brand{left:100px;top:2215px;width:200px;height:150px;display:flex;align-items:center;justify-content:center}
.foot-brand span{font-family:"Poppins",sans-serif;font-weight:600;font-size:26px;color:var(--white);line-height:1.1}
.foot-h{font-family:"Arimo",sans-serif;font-weight:700;font-size:17px;color:var(--white)}
.foot-text{font-size:12px;line-height:22px;color:var(--white)}
.contact-row{display:flex;align-items:flex-start;gap:12px;font-size:12px;line-height:17px;color:var(--white)}
.email-field{left:885px;top:2310px;width:229px;height:34px;background:var(--white);color:#666;font-size:13px;padding:8px 14px}
.sub-btn{left:885px;top:2354px;width:82px;height:27px;background:var(--green);font-family:"Poppins",sans-serif;font-size:10px;font-weight:600;text-align:center;line-height:27px;color:var(--white)}
.foot-rule{left:86px;top:2415px;width:1028px;height:1px;background:rgba(255,255,255,.25)}
.social{width:36px;height:36px;border-radius:50%;border:2px solid var(--white)}
</style>
</head>
<body>
<div class="abs top-line"></div>
<header class="abs site-header"></header>
<div class="abs brand-disc"><div class="brand-name">Solvane<br>Energy</div></div>
<nav>
  <span class="abs main-nav active" style="left:452px">HOME</span>
  <span class="abs main-nav" style="left:536px">ABOUT US</span>
  <span class="abs main-nav" style="left:646px">SERVICES</span>
  <span class="abs main-nav" style="left:751px">TESTIMONIALS</span>
  <span class="abs main-nav" style="left:887px">VIDEO</span>
  <span class="abs main-nav" style="left:971px">CONTACT US</span>
</nav>
<div class="abs search-btn"><svg width="16" height="16" viewBox="0 0 16 16"><circle cx="6.5" cy="6.5" r="4.5" fill="none" stroke="var(--green)" stroke-width="2"/><line x1="10" y1="10" x2="14" y2="14" stroke="var(--green)" stroke-width="2"/></svg></div>

<div class="abs hero" role="img" aria-label="Photo of a large suburban home with a driveway under a blue sky"></div>
<h1 class="abs hero-title">SOLVANE ENERGY</h1>
<p class="abs hero-sub">SED UT PERSPICIATIS UNDE OMNIS ISTE NATUS ERROR SIT VOLUPTATEM</p>
<svg class="abs play" width="84" height="84" viewBox="0 0 84 84"><circle cx="42" cy="42" r="39" fill="none" stroke="#fff" stroke-width="3"/><polygon points="34,28 58,42 34,56" fill="#fff"/></svg>

<form class="abs lead-form">
  <h2>Calculate Savings</h2>
  <div class="field" style="top:76px">First Name :</div>
  <div class="field" style="top:123px">Last Name :</div>
  <div class="field" style="top:169px">Phone :</div>
  <div class="field" style="top:216px">Zip Code :</div>
  <div class="submit">SUBMIT</div>
</form>

<h2 class="abs section-title" style="top:832px">Welcome to Solvane Energy</h2>
<p class="abs section-lede" style="top:879px">Sed ut perspiciatis unde omnis iste natus error sit voluptatem accusantium doloremque laudantium, totam rem aperiam, eaque ipsa quae ab illo inventore veritatis et quasi architecto beatae vitae dicta sunt explicabo.</p>

<svg class="abs" style="left:0;top:950px" width="1200" height="170" viewBox="0 950 1200 170">
  <g fill="none" stroke-width="6">
    <path d="M188 962 A72 72 0 0 1 188 1105" stroke="var(--green)"/><path d="M188 1105 A72 72 0 0 1 188 962" stroke="var(--blue)"/>
    <path d="M456 962 A72 72 0 0 1 456 1105" stroke="var(--green)"/><path d="M456 1105 A72 72 0 0 1 456 962" stroke="var(--blue)"/>
    <path d="M735 962 A72 72 0 0 1 735 1105" stroke="var(--green)"/><path d="M735 1105 A72 72 0 0 1 735 962" stroke="var(--blue)"/>
    <circle cx="1011" cy="1033" r="72" stroke="var(--green)"/>
  </g>
  <g fill="#eef6fb"><circle cx="188" cy="1033" r="44"/><circle cx="456" cy="1033" r="44"/><circle cx="735" cy="1033" r="44"/><circle cx="1011" cy="1033" r="44" fill="#f1f8e6"/></g>
  <g fill="var(--green)"><circle cx="255" cy="1033" r="13"/><circle cx="456" cy="1100" r="13"/><circle cx="668" cy="1033" r="13"/><circle cx="1011" cy="966" r="13"/></g>
  <g fill="#fff" font-family="Poppins,sans-serif" font-size="13" font-weight="600" text-anchor="middle"><text x="255" y="1038">1</text><text x="456" y="1105">2</text><text x="668" y="1038">3</text><text x="1011" y="971">4</text></g>
  <g fill="none" stroke="#aaa" stroke-width="1.5" stroke-dasharray="3 3"><path d="M285 1045 Q320 1015 360 1033"/><path d="M552 1045 Q590 1015 628 1033"/><path d="M835 1045 Q870 1015 910 1033"/></g>
  <g fill="#aaa"><polygon points="362,1033 352,1028 354,1038"/><polygon points="630,1033 620,1028 622,1038"/><polygon points="912,1033 902,1028 904,1038"/></g>
</svg>
<div class="abs step" style="left:78px;top:1141px"><h3>Speak to a<br>solar consultant</h3><p>Sed ut perspiciatis unde omnis iste natus error sit voluptatem</p></div>
<div class="abs step" style="left:346px;top:1141px"><h3>We'll design your<br>solar panel system</h3><p>Sed ut perspiciatis unde omnis iste natus error sit voluptatem</p></div>
<div class="abs step" style="left:625px;top:1141px"><h3>Schedule your<br>1 day install</h3><p>Sed ut perspiciatis unde omnis iste natus error sit voluptatem</p></div>
<div class="abs step" style="left:901px;top:1141px"><h3>Start saving on your<br>electricity bill</h3><p>Sed ut perspiciatis unde omnis iste natus error sit voluptatem</p></div>

<section class="abs testimonials"></section>
<h2 class="abs section-title" style="top:1326px">Our Testimonials</h2>
<p class="abs section-lede" style="top:1374px">Sed ut perspiciatis unde omnis iste natus error sit voluptatem accusantium doloremque laudantium, totam rem aperiam, eaque ipsa</p>

<div class="abs avatar" style="left:88px;top:1459px" role="img" aria-label="Portrait of a smiling customer"></div>
<p class="abs quote" style="left:196px;top:1462px"><b>“</b>Sed ut perspiciatis unde omnis iste natus error sit voluptatem accusantium doloremque laudantium, totam rem vitae dicta sunt explicabo.</p>
<div class="abs reviewer" style="left:196px;top:1570px">JHON SMITH</div>
<div class="abs posted" style="left:196px;top:1591px">POSTED ON 25 AUG 2017</div>
<div class="abs stars" style="left:196px;top:1610px">☆☆☆☆★</div>

<div class="abs avatar" style="left:438px;top:1459px" role="img" aria-label="Portrait of a smiling customer"></div>
<p class="abs quote" style="left:546px;top:1462px"><b>“</b>Sed ut perspiciatis unde omnis iste natus error sit voluptatem accusantium doloremque laudantium, totam rem vitae dicta sunt explicabo.</p>
<div class="abs reviewer" style="left:546px;top:1570px">JHON SMITH</div>
<div class="abs posted" style="left:546px;top:1591px">POSTED ON 25 AUG 2017</div>
<div class="abs stars" style="left:546px;top:1610px">☆☆☆☆★</div>

<div class="abs avatar" style="left:789px;top:1459px" role="img" aria-label="Portrait of a smiling customer"></div>
<p class="abs quote" style="left:897px;top:1462px"><b>“</b>Sed ut perspiciatis unde omnis iste natus error sit voluptatem accusantium doloremque laudantium, totam rem vitae dicta sunt explicabo.</p>
<div class="abs reviewer" style="left:897px;top:1570px">JHON SMITH</div>
<div class="abs posted" style="left:897px;top:1591px">POSTED ON 25 AUG 2017</div>
<div class="abs stars" style="left:897px;top:1610px">☆☆☆☆★</div>

<h2 class="abs section-title" style="top:1716px">Latest Blog</h2>
<p class="abs section-lede" style="top:1764px">Sed ut perspiciatis unde omnis iste natus error sit voluptatem accusantium doloremque laudantium, totam rem aperiam, eaque ipsa</p>

<div class="abs blog-img" style="left:86px;top:1814px;background:linear-gradient(160deg,#f3d98a 0%,#5b7fb0 45%,#1e3558 100%)" role="img" aria-label="Photo of solar panels in a field at sunset"></div>
<div class="abs blog-img" style="left:437px;top:1814px;background:linear-gradient(180deg,#3f8fe0 0%,#8fc3f0 45%,#1f4f9a 100%)" role="img" aria-label="Photo of solar panels under a bright blue sky"></div>
<div class="abs blog-img" style="left:785px;top:1814px;background:linear-gradient(180deg,#cfe3f2 0%,#b9a58c 55%,#8a4a34 100%)" role="img" aria-label="Photo of a brick house with rooftop solar panels"></div>

<h3 class="abs blog-title" style="left:86px;top:2032px">Neque porro quisquam</h3>
<h3 class="abs blog-title" style="left:437px;top:2032px">Neque porro quisquam</h3>
<h3 class="abs blog-title" style="left:785px;top:2032px">Neque porro quisquam</h3>
<p class="abs blog-text" style="left:86px;top:2069px">Sed ut perspiciatis unde omnis iste natus error sit voluptatem accusantiumue ipsa beatae vitae dicta sunt explicabo.</p>
<p class="abs blog-text" style="left:437px;top:2069px">Sed ut perspiciatis unde omnis iste natus error sit voluptatem accusantiumue ipsa beatae vitae dicta sunt explicabo.</p>
<p class="abs blog-text" style="left:785px;top:2069px">Sed ut perspiciatis unde omnis iste natus error sit voluptatem accusantiumue ipsa beatae vitae dicta sunt explicabo.</p>

<div class="abs blog-meta" style="left:86px;top:2130px"><svg width="12" height="12" viewBox="0 0 12 12"><rect x="1" y="2" width="10" height="9" fill="none" stroke="var(--green)"/><line x1="1" y1="5" x2="11" y2="5" stroke="var(--green)"/></svg>1 month ago&nbsp;&nbsp;&nbsp;<svg width="12" height="12" viewBox="0 0 12 12"><path d="M6 1.5c2.8 0 5 1.8 5 4s-2.2 4-5 4l-3 2v-2.7C1.8 8 1 6.9 1 5.5c0-2.2 2.2-4 5-4z" fill="none" stroke="var(--green)"/></svg>05 Comments</div>
<div class="abs blog-meta" style="left:437px;top:2130px"><svg width="12" height="12" viewBox="0 0 12 12"><rect x="1" y="2" width="10" height="9" fill="none" stroke="var(--green)"/><line x1="1" y1="5" x2="11" y2="5" stroke="var(--green)"/></svg>1 month ago&nbsp;&nbsp;&nbsp;<svg width="12" height="12" viewBox="0 0 12 12"><path d="M6 1.5c2.8 0 5 1.8 5 4s-2.2 4-5 4l-3 2v-2.7C1.8 8 1 6.9 1 5.5c0-2.2 2.2-4 5-4z" fill="none" stroke="var(--green)"/></svg>05 Comments</div>
<div class="abs blog-meta" style="left:785px;top:2130px"><svg width="12" height="12" viewBox="0 0 12 12"><rect x="1" y="2" width="10" height="9" fill="none" stroke="var(--green)"/><line x1="1" y1="5" x2="11" y2="5" stroke="var(--green)"/></svg>1 month ago&nbsp;&nbsp;&nbsp;<svg width="12" height="12" viewBox="0 0 12 12"><path d="M6 1.5c2.8 0 5 1.8 5 4s-2.2 4-5 4l-3 2v-2.7C1.8 8 1 6.9 1 5.5c0-2.2 2.2-4 5-4z" fill="none" stroke="var(--green)"/></svg>05 Comments</div>

<footer class="abs site-footer"></footer>
<div class="abs foot-brand"><span>Solvane<br>Energy</span></div>

<h4 class="abs foot-h" style="left:378px;top:2212px">INFORMATION</h4>
<div class="abs foot-text" style="left:378px;top:2253px">AUGUST 21, 2017</div>
<p class="abs foot-text" style="left:378px;top:2280px;width:220px">Sed ut perspiciatis unde omnis iste natus error sit voluptatem accusan-tium doloremque</p>
<div class="abs foot-text" style="left:378px;top:2354px;text-decoration:underline">Read More</div>

<h4 class="abs foot-h" style="left:637px;top:2214px">CONTACT US</h4>
<div class="abs contact-row" style="left:640px;top:2264px"><svg width="12" height="12"><rect x="1" y="3" width="10" height="8" rx="1" fill="#fff"/></svg>(000)-121-1231 &nbsp;(Phone)</div>
<div class="abs contact-row" style="left:640px;top:2294px"><svg width="12" height="12"><rect x="1" y="4" width="10" height="6" fill="#fff"/><rect x="3" y="1" width="6" height="3" fill="#fff"/></svg>(000)-121-1231 &nbsp;(Fax)</div>
<div class="abs contact-row" style="left:640px;top:2324px"><svg width="12" height="12"><rect x="1" y="3" width="10" height="7" fill="none" stroke="#fff"/><polyline points="1,3 6,7 11,3" fill="none" stroke="#fff"/></svg><span style="text-decoration:underline">info@solvaneenergy.com</span></div>
<div class="abs contact-row" style="left:640px;top:2352px"><svg width="12" height="14"><path d="M6 1a4 4 0 0 1 4 4c0 3-4 8-4 8S2 8 2 5a4 4 0 0 1 4-4z" fill="#fff"/></svg><span># 14 Lorem Ipsum Dummy<br>Lorem Ipsum</span></div>

<h4 class="abs foot-h" style="left:885px;top:2212px">NEWSLETTER</h4>
<p class="abs foot-text" style="left:885px;top:2252px;width:230px">Register Your email address to get information ablout us</p>
<div class="abs email-field">Email Address</div>
<div class="abs sub-btn">SUBSCRIBE</div>

<div class="abs foot-rule"></div>
<div class="abs foot-text" style="left:86px;top:2442px">© Copyright 2017 Solvane Energy.All Rights Reserved</div>
<div class="abs social" style="left:905px;top:2435px"></div>
<div class="abs social" style="left:948px;top:2435px"></div>
<div class="abs social" style="left:990px;top:2435px"></div>
<div class="abs social" style="left:1033px;top:2435px"></div>
<div class="abs social" style="left:1076px;top:2435px"></div>
</body>
</html>
```